I will ask the design of the business card

We are looking for business card design of the new company "R DOVE PAYGRID WORKS LLC." Based in Azerbaijan.
In case
We are working on Azerbaijan to set up the first exchange of crypto currencies.

The key currency used in exchanges is called "PLUME".
In case
We are doing project to make crypto currency infrastructure.

We provide state-of-the-art technology to the world.

```html
<!DOCTYPE html>
<html lang="en">
<head>
<meta charset="utf-8">
<title>R Dove Paygrid Works LLC – Business Card</title>
<link rel="stylesheet" href="https://fonts.googleapis.com/css2?family=Bebas+Neue&family=Source+Sans+3:wght@400;600&display=swap">
<style>
  :root {
    --backdrop: #9a9a9a;
    --card-dark: #0b0a0b;
    --gold: #f2b83c;
    --amber-top: #e0a046;
    --amber-bottom: #e4c640;
    --ink: #111111;
    --light-text: #e6e6e6;
    --rule: #5a5a5a;
  }
  * { margin: 0; padding: 0; box-sizing: border-box; }
  html, body {
    width: 1200px; height: 900px; overflow: hidden;
    background: var(--backdrop);
  }
  .canvas { position: relative; width: 1200px; height: 900px; }

  .card {
    position: absolute;
    width: 477px; height: 295px;
    box-shadow: 3px 4px 6px rgba(0,0,0,0.35);
  }
  .card-front {
    left: 120px; top: 275px;
    background: var(--card-dark);
    border-radius: 0 46px 0 46px;
  }
  .card-back {
    left: 607px; top: 273px;
    background: linear-gradient(to bottom, var(--amber-top), var(--amber-bottom));
    border-radius: 46px 0 46px 0;
  }

  .company-name {
    font-family: "Bebas Neue", sans-serif;
    font-size: 40px;
    line-height: 1;
    letter-spacing: 0.3px;
    white-space: nowrap;
  }
  .card-front .company-name {
    position: absolute; right: 32px; top: 84px;
    color: var(--gold);
  }
  .card-back .company-name {
    position: absolute; left: 0; right: 0; top: 130px;
    text-align: center; color: var(--ink);
  }

  .person { position: absolute; left: 30px; top: 161px; }
  .person-name {
    font-family: "Bebas Neue", sans-serif;
    font-size: 22px; line-height: 1; color: var(--gold);
  }
  .person-title {
    font-family: "Source Sans 3", sans-serif;
    font-size: 13px; line-height: 1; color: var(--light-text);
    margin-top: 1px;
  }
  .title-rule {
    position: absolute; left: 148px; top: 190px;
    width: 297px; height: 1px; background: var(--rule);
  }

  .body-text {
    font-family: "Source Sans 3", sans-serif;
    font-size: 13px; line-height: 17.5px; color: var(--light-text);
  }
  .address { position: absolute; left: 31px; top: 235px; }

  .contacts { position: absolute; right: 31px; top: 200px; list-style: none; }
  .contacts li { display: flex; justify-content: flex-end; align-items: center; gap: 3px; }
  .contacts svg { width: 11px; height: 11px; fill: var(--gold); }

  .back-website {
    position: absolute; left: 0; right: 0; top: 247px;
    text-align: center;
    font-family: "Source Sans 3", sans-serif;
    font-size: 13px; color: var(--ink);
  }
</style>
</head>
<body>
<main class="canvas">

  <section class="card card-front" aria-label="Card front">
    <h1 class="company-name">R DOVE PAYGRID WORKS LLC</h1>

    <div class="person">
      <p class="person-name">MARCUS HALE</p>
      <p class="person-title">Managing Director</p>
    </div>
    <div class="title-rule"></div>

    <ul class="contacts body-text">
      <li>044-987 654 321
        <svg viewBox="0 0 12 12" aria-hidden="true"><path d="M1 4c0-2 2-3 5-3s5 1 5 3l-3 1-1-1.3H5L4 5 1 4zM2.5 6h7l1 5h-9l1-5zm3.5 1.3a1.6 1.6 0 1 0 0 3.2 1.6 1.6 0 0 0 0-3.2z"/></svg>
      </li>
      <li>044-987 654 321
        <svg viewBox="0 0 12 12" aria-hidden="true"><path d="M3.5 0h5a1 1 0 0 1 1 1v10a1 1 0 0 1-1 1h-5a1 1 0 0 1-1-1V1a1 1 0 0 1 1-1zm.3 1.5v7.5h4.4V1.5H3.8zM6 9.8a.7.7 0 1 0 0 1.4.7.7 0 0 0 0-1.4z"/></svg>
      </li>
      <li>info@dovepaygrid.com
        <svg viewBox="0 0 12 12" aria-hidden="true"><path d="M0 2.5h12v7H0v-7zm1 .8L6 7l5-3.7v-.1H1v.1z"/></svg>
      </li>
      <li>www.dovepaygrid.com
        <svg viewBox="0 0 12 12" aria-hidden="true"><circle cx="6" cy="6" r="5.5"/><path d="M3 3.5l2 .5 1 2-1.5 1 .5 2.5L3 8z M7.5 2.5l2 1.5-.5 2-1.5-.5z" fill="var(--card-dark)"/></svg>
      </li>
    </ul>

    <address class="address body-text" style="font-style:normal">
      12345, Address Goes Here<br>
      Country Name, 123456
    </address>
  </section>

  <section class="card card-back" aria-label="Card back">
    <h2 class="company-name">R DOVE PAYGRID WORKS LLC</h2>
    <p class="back-website">www.dovepaygrid.com</p>
  </section>

</main>
</body>
</html>
```